Brookvane Consulting Business Card Design

Business Card Design for Brookvane Consulting. Brookvane Consulting is a boutique consultancy based in Atlanta, GA., that specializes in marketing strategy, organization planning, and leadership development. We provide solutions for small businesses and startups as well as Vantage 300 companies.

http://brookvaneconsulting.com/

Target Market(s)

We provide solutions for small businesses and startups as well as Vantage 300 companies.

Industry/Entity Type

Consulting

Contact Information for Business Card

Two sided business card with priority on contact information, logo, tag line (Guidance to Plan Better, Act Sooner, Grow Further)

Colors

Designer to choose colors to be used in the design.

Requirements
Must have
• contact information, logo, tag line (Guidance to Plan Better, Act Sooner, Grow Further)
• Simple no over communication.
Nice to have
• I would like to see different placements of logo and creative use of both sides of the card
Should not have
• Do not put too much information on the card.

```html
<!DOCTYPE html>
<html lang="en">
<head>
<meta charset="utf-8">
<title>Brookvane Consulting Business Card</title>
<link rel="stylesheet" href="https://fonts.googleapis.com/css2?family=Montserrat:wght@400;500;600&display=swap">
<style>
  :root {
    --backdrop: #262626;
    --card: #353535;
    --ink-light: #f4f4f4;
    --ink-front: #bdbdbd;
    --ink-muted: #e6e6e6;
  }
  * { margin: 0; padding: 0; box-sizing: border-box; }
  html, body { width: 799px; height: 1200px; overflow: hidden; }
  body {
    background: var(--backdrop);
    font-family: "Montserrat", sans-serif;
    position: relative;
  }
  .card {
    position: absolute;
    left: 65px;
    width: 670px;
    height: 383px;
    background: var(--card);
    border-radius: 30px;
    box-shadow: 0 10px 30px rgba(0,0,0,0.35);
  }
  .card-front { top: 140px; }
  .card-back { top: 680px; }

  .wordmark {
    font-weight: 600;
    font-size: 44px;
    letter-spacing: 0.5px;
    line-height: 1;
    white-space: nowrap;
  }
  .card-front .wordmark {
    position: absolute;
    top: 50%;
    left: 50%;
    transform: translate(-50%, -50%);
    color: var(--ink-front);
  }
  .card-back .brand {
    position: absolute;
    top: 62px;
    right: 40px;
    text-align: right;
  }
  .card-back .wordmark { color: var(--ink-light); font-size: 38px; }
  .tagline {
    margin-top: 12px;
    font-size: 13px;
    font-weight: 400;
    color: var(--ink-muted);
    letter-spacing: 0.3px;
    white-space: nowrap;
  }
  .contact {
    position: absolute;
    left: 48px;
    bottom: 70px;
    color: var(--ink-muted);
  }
  .contact-name {
    font-size: 20px;
    font-weight: 600;
    color: var(--ink-light);
    margin-bottom: 16px;
  }
  .contact-line {
    font-size: 14px;
    line-height: 1.55;
  }
</style>
</head>
<body>
  <section class="card card-front" aria-label="Card front">
    <div class="wordmark">Brookvane Consulting</div>
  </section>

  <section class="card card-back" aria-label="Card back">
    <div class="brand">
      <div class="wordmark">Brookvane Consulting</div>
      <p class="tagline">Guidance to Plan Better, Act Sooner, Grow Further</p>
    </div>
    <div class="contact">
      <p class="contact-name">Dario</p>
      <p class="contact-line">424-555-0192</p>
      <p class="contact-line">dario@brookvaneconsulting.com</p>
      <p class="contact-line">www.brookvaneconsulting.com</p>
    </div>
  </section>
</body>
</html>
```